RWT Fittings Ltd Business Cards

We need a business card with our business logo. We provide window and door installations on high-rises in west coast British Colombia, Canada.

I would like my business information and details on one side of the card, and the other side the company name with logo

Target Market(s)

General Contractors

Industry/Entity Type

Construction

Contact Information for Business Card

one side i want my company name and logo in the dark theme logo that i provided

Requirements
Must have
• Marco Peltieri, 16045518293, RWTFittings@mailbox-demo.com, 1407-5194 Linden Row Burnaby BC, V5H 2K9, Owner & Manager

```html
<!DOCTYPE html>
<html lang="en">
<head>
<meta charset="utf-8">
<title>RWT Fittings Ltd Business Cards</title>
<link rel="stylesheet" href="https://fonts.googleapis.com/css2?family=Roboto:wght@400;500;700&display=swap">
<style>
  :root {
    --stage: #222223;
    --card-dark: #1f2024;
    --brand-blue: #29a9e1;
    --name-grey: #8c8c8e;
    --text-white: #f2f2f2;
    --photo-deep: #1c1a18;
    --photo-warm: #4a433c;
  }
  * { box-sizing: border-box; margin: 0; padding: 0; }
  html, body {
    width: 1200px; height: 780px; overflow: hidden;
    background: var(--stage);
    font-family: "Roboto", Arial, sans-serif;
  }
  .sheet {
    position: relative; width: 1200px; height: 780px;
    display: flex; align-items: center; justify-content: center; gap: 48px;
  }
  .card {
    position: relative; width: 532px; height: 304px; overflow: hidden;
    border-radius: 3px;
    box-shadow: 0 18px 40px rgba(0,0,0,.55);
  }

  /* Contact side */
  .card--contact { background: var(--card-dark); }
  .card--contact .brand {
    position: absolute; left: 34px; top: 34px;
    display: flex; align-items: center; gap: 10px;
  }
  .brand__square { width: 18px; height: 18px; background: var(--brand-blue); }
  .brand__name {
    color: var(--brand-blue); font-weight: 700; font-size: 24px; letter-spacing: .5px;
  }
  .contact {
    position: absolute; right: 40px; bottom: 28px; text-align: right;
    color: var(--text-white);
  }
  .contact__name { font-weight: 700; font-size: 25px; line-height: 1.1; }
  .contact__first { color: var(--brand-blue); }
  .contact__last { color: var(--name-grey); }
  .contact__title { font-weight: 500; font-size: 13px; margin-top: 2px; }
  .contact__address { font-size: 13px; line-height: 1.4; margin-top: 14px; }
  .contact__line {
    font-size: 13px; margin-top: 10px;
    display: flex; align-items: center; justify-content: flex-end; gap: 8px;
  }
  .contact__line + .contact__line { margin-top: 6px; }
  .contact__icon { width: 13px; height: 13px; fill: var(--brand-blue); }
  .accent-bar {
    position: absolute; right: 0; top: 150px; width: 12px; height: 52px;
    background: var(--brand-blue);
  }

  /* Brand side */
  .card--brand {
    background: linear-gradient(120deg, var(--photo-deep) 0%, #2b2723 40%, var(--photo-warm) 75%, #3a342f 100%);
  }
  .card--brand .photo { position: absolute; inset: 0; }
  .card--brand .brand {
    position: absolute; inset: 0;
    display: flex; align-items: center; justify-content: center; gap: 12px;
  }
  .card--brand .brand__name { font-size: 34px; }
  .card--brand .brand__square { width: 24px; height: 24px; }
</style>
</head>
<body>
<main class="sheet">
  <section class="card card--contact" aria-label="Business card, contact side">
    <div class="brand">
      <span class="brand__square"></span>
      <span class="brand__name">RWT Fittings Ltd</span>
    </div>
    <span class="accent-bar"></span>
    <div class="contact">
      <p class="contact__name"><span class="contact__first">Marco</span> <span class="contact__last">Peltieri</span></p>
      <p class="contact__title">Owner &amp; Manager</p>
      <p class="contact__address">1407-5194 Linden Row<br>Burnaby BC, V5H 2K9</p>
      <p class="contact__line">1604 551 8293
        <svg class="contact__icon" viewBox="0 0 24 24" aria-hidden="true"><path d="M6.6 10.8a15 15 0 0 0 6.6 6.6l2.2-2.2c.3-.3.7-.4 1-.2 1.1.4 2.3.6 3.6.6.6 0 1 .4 1 1V20c0 .6-.4 1-1 1A17 17 0 0 1 3 4c0-.6.4-1 1-1h3.5c.6 0 1 .4 1 1 0 1.3.2 2.5.6 3.6.1.3 0 .7-.2 1z"/></svg>
      </p>
      <p class="contact__line">RWTFittings@mailbox-demo.com
        <svg class="contact__icon" viewBox="0 0 24 24" aria-hidden="true"><path d="M2 5h20v14H2zm2 2v.5l8 5 8-5V7zm0 2.8V17h16V9.8l-8 5z"/></svg>
      </p>
    </div>
  </section>

  <section class="card card--brand" aria-label="Business card, brand side">
    <div class="photo" role="img" aria-label="Dim interior photograph of a modern room with a plant, used as card background"></div>
    <div class="brand">
      <span class="brand__square"></span>
      <span class="brand__name">RWT Fittings Ltd</span>
    </div>
  </section>
</main>
</body>
</html>
```